Business Card for Financial Asset Management Company

Now we are launching a new company based in Tokyo.
The company information is below;

Company Name: Velmora Advisory

Operations: Financial assets management, Proposing forming portfolio of assets, Consulting service, and advising to enhance your company's financial health

Corporate Colour: Japan Blue or Navy like below
http://stuweb.ax.tolvaric.edu/kpimra/pics/Shade/Mist-Shade-217.jpg

It's dark and deep, and will get to fit to our clients as our relationships last longer and longer.

Our images for this colour are "Japanese style" and "pride in our craftmanship" , and also "gentle".

Corporate Key Image: an order taker who is sincere, polite, but courageous

We don't have our logo yet so please feel free to put any symbol on your design.

Please do not hesitate about asking any questions.
Thank you :-)

Reason: We are still discussin on final decision. Thank you for your understanding.

```html
<!DOCTYPE html>
<html lang="en">
<head>
<meta charset="utf-8">
<title>Velmora Advisory – Business Card</title>
<link rel="stylesheet" href="https://fonts.googleapis.com/css2?family=Open+Sans:wght@300;400;600;700&display=swap">
<style>
  :root {
    --paper: #ffffff;
    --navy: #1f3c99;
    --band-light: #163f95;
    --band-dark: #1a3283;
    --band-edge: #15307f;
    --ink-light: #ffffff;
  }
  * { margin: 0; padding: 0; box-sizing: border-box; }
  html, body { width: 1200px; height: 726px; overflow: hidden; background: var(--paper); }
  .card {
    position: relative;
    width: 1200px;
    height: 726px;
    background: var(--paper);
    font-family: "Open Sans", Arial, sans-serif;
    overflow: hidden;
  }
  .band { position: absolute; inset: 0; }
  .brand-dot {
    position: absolute;
    left: 82px; top: 99px;
    width: 104px; height: 104px;
    border-radius: 50%;
    background: var(--navy);
  }
  .brand-name {
    position: absolute;
    left: 240px; top: 98px;
    font-size: 56px;
    font-weight: 600;
    line-height: 50px;
    color: var(--navy);
  }
  .divider {
    position: absolute;
    left: 188px; top: 288px;
    width: 2px; height: 362px;
    background: var(--ink-light);
  }
  .person-name {
    position: absolute;
    left: 237px; top: 353px;
    font-size: 36px; font-weight: 700; line-height: 1;
    color: var(--ink-light);
  }
  .person-role {
    position: absolute;
    left: 237px; top: 406px;
    font-size: 29px; font-weight: 400; line-height: 1;
    color: var(--ink-light);
  }
  .contact {
    position: absolute;
    left: 237px; top: 474px;
    font-size: 30px; font-weight: 300; line-height: 47px;
    color: var(--ink-light);
    list-style: none;
  }
  .contact .sep { margin: 0 14px; }
</style>
</head>
<body>
  <div class="card">
    <svg class="band" width="1200" height="726" viewBox="0 0 1200 726" aria-hidden="true">
      <defs>
        <linearGradient id="bandFill" x1="0" y1="0" x2="0" y2="1">
          <stop offset="0" stop-color="var(--band-light)" style="stop-color:#163f95"/>
          <stop offset="1" stop-color="var(--band-dark)" style="stop-color:#1a3283"/>
        </linearGradient>
      </defs>
      <path d="M0 323 L84 323 Q256 244 428 303 Q599 254 770 301 Q943 254 1116 328 L1200 324 L1200 726 L0 726 Z"
            fill="url(#bandFill)" stroke="#15307f" stroke-width="4"/>
    </svg>

    <div class="brand-dot" aria-hidden="true"></div>
    <div class="brand-name">Velmora<br>Advisory</div>

    <div class="divider"></div>
    <h1 class="person-name">Haruka Sena</h1>
    <p class="person-role">General Director</p>
    <ul class="contact">
      <li>haruka.sena@velmoraadvisory.jp</li>
      <li>Tel. 090 555 0142<span class="sep">|</span>Fax. 090 555 0178</li>
      <li>Kanda Meridian Tower</li>
      <li>2-7, Nishikanda 3-Chome, Chiyoda-ku, Tokyo 101-0065</li>
    </ul>
  </div>
</body>
</html>
```